furniture and home contents restoration

I need to list the services that we perform in our studio.
we serve the general public as well as the insurance/ remediation industry

```html
<!DOCTYPE html>
<html lang="en">
<head>
<meta charset="utf-8">
<title>Northgate Refinishers – Business Card</title>
<link rel="stylesheet" href="https://fonts.googleapis.com/css2?family=Crimson+Text:wght@400;700&display=swap">
<style>
  :root {
    --ink: #1f313b;
    --paper: #ffffff;
    --card-dark: #1e313b;
    --on-dark: #f1f3f4;
    --backdrop: #e4e4e3;
    --serif: "Crimson Text", "Times New Roman", serif;
  }
  * { box-sizing: border-box; margin: 0; padding: 0; }
  html, body { width: 1200px; height: 801px; overflow: hidden; }
  body {
    background: var(--backdrop);
    font-family: var(--serif);
    display: flex;
    align-items: center;
    justify-content: center;
    gap: 40px;
  }
  .card {
    width: 540px;
    height: 309px;
    position: relative;
    box-shadow: 0 6px 18px rgba(0,0,0,.18);
  }

  /* Front face */
  .card--front { background: var(--paper); color: var(--ink); }
  .front__brand {
    position: absolute; left: 34px; top: 74px; width: 190px;
    font-weight: 700; font-size: 31px; line-height: 1.02;
    letter-spacing: .5px; text-transform: uppercase;
  }
  .front__divider {
    position: absolute; left: 232px; top: 30px;
    width: 1.5px; height: 150px; background: var(--ink);
  }
  .front__details { position: absolute; left: 250px; top: 26px; right: 20px; }
  .front__name {
    font-weight: 700; font-size: 19px; letter-spacing: 1px;
    text-transform: uppercase; margin-bottom: 6px;
  }
  .contact-list { list-style: none; font-size: 12.5px; line-height: 1.28; }
  .contact-list li { display: flex; align-items: center; gap: 6px; }
  .contact-list svg { width: 9px; height: 9px; flex: none; fill: var(--ink); }
  .front__tagline { font-size: 12.5px; line-height: 1.25; margin-top: 12px; }
  .front__service {
    position: absolute; left: 34px; right: 20px; bottom: 52px;
    font-size: 26px; letter-spacing: .6px; text-transform: uppercase;
    text-align: right;
  }

  /* Back face */
  .card--back {
    background: var(--card-dark); color: var(--on-dark);
    padding: 20px 26px 18px;
    display: flex; flex-direction: column;
  }
  .back__brand {
    text-align: center; font-weight: 700; font-size: 25px;
    letter-spacing: .8px; text-transform: uppercase; margin-bottom: 10px;
  }
  .services { display: flex; gap: 18px; flex: 1; }
  .services ul {
    list-style: none; flex: 1;
    font-size: 10.4px; line-height: 1.33; text-transform: uppercase; letter-spacing: .2px;
  }
  .services li::before { content: "• "; }
  .back__offer {
    text-align: center; font-size: 12.5px; line-height: 1.25;
    text-transform: uppercase; letter-spacing: .4px;
  }
</style>
</head>
<body>

  <section class="card card--front" aria-label="Card front">
    <h1 class="front__brand">Northgate<br>Refinishers</h1>
    <div class="front__divider"></div>
    <div class="front__details">
      <h2 class="front__name">Daniel Moretti</h2>
      <ul class="contact-list">
        <li><svg viewBox="0 0 10 10" aria-hidden="true"><path d="M2 0.5 L4 2.8 L3 4 Q4 6 6 7 L7.2 6 L9.5 8 L8 9.6 Q3 9 0.4 2 Z"/></svg>555 010 2400</li>
        <li><svg viewBox="0 0 10 10" aria-hidden="true"><path d="M2.5 0 H7.5 V10 H2.5 Z M3.5 1 V7.5 H6.5 V1 Z"/></svg>555 010 7831</li>
        <li><svg viewBox="0 0 10 10" aria-hidden="true"><path d="M1 3 H9 V9 H1 Z M3 0.5 H7 V3 H3 Z"/></svg>555 010 3640</li>
        <li><svg viewBox="0 0 10 10" aria-hidden="true"><path d="M5 0 A3.6 3.6 0 0 1 8.6 3.6 C8.6 6 5 10 5 10 C5 10 1.4 6 1.4 3.6 A3.6 3.6 0 0 1 5 0 Z"/></svg>12 elm hollow rd. riverton, ny 10000</li>
        <li><svg viewBox="0 0 10 10" aria-hidden="true"><path d="M0.5 2 H9.5 V8.5 H0.5 Z M1.5 3 L5 5.8 L8.5 3 Z" fill-rule="evenodd"/></svg>northgate@example.com</li>
      </ul>
      <p class="front__tagline">serving the general public and the<br>insurance industry for over 40 years</p>
    </div>
    <p class="front__service">Home Contents Restoration</p>
  </section>

  <section class="card card--back" aria-label="Card back">
    <h2 class="back__brand">Northgate Refinishers</h2>
    <div class="services">
      <ul>
        <li>Furniture repair and restoration</li>
        <li>Art cleaning and remounting</li>
        <li>Art and mirror frame repair</li>
        <li>Chandelier cleaning and restoration</li>
        <li>Document restoration</li>
        <li>Glass, ceramic, and mirror repair</li>
        <li>Hardware repair and restoration</li>
        <li>Kitchen removal and reinstallation</li>
        <li>Lamp cleaning and restoration</li>
        <li>Lamp shade replacement</li>
      </ul>
      <ul>
        <li>Metal polishing and restoration</li>
        <li>Odor removal and ozone services</li>
        <li>Photo restoration</li>
        <li>Upholstery cleaning and deodorizing</li>
        <li>In-house upholstery and reupholstery</li>
        <li>Rug cleaning and restoration</li>
        <li>Musical instrument restoration</li>
        <li>Window treatment repair/ restoration</li>
        <li>Leather restoration and replacement</li>
        <li>Piano restoration and repair</li>
      </ul>
    </div>
    <p class="back__offer">On-site inspections and desk review services<br>Assessment reports and estimates for repair and restoration</p>
  </section>

</body>
</html>
```